Homemaking training schools needs a Business Card design

Designer, Hello!

No special requirements, good-looking enough.
--------------------------------------------------------------------------

Name: Marcus Dole
Chairman
Tel: 0574-71948263
Mobile: 13857420916
Email: kelvora@mailnest.example
Web: www.prt2019.example
Add: No.258, LanpingJie, BeiyuanQu, Ningbo, Zhejiang

LOGO
Ningbo PRT Homemaking Training School

Target Market(s)

pregnant women, mothers, infants, the elderly and families, including cleaning, cooking, nursing training.

Industry/Entity Type

Business

Contact Information for Business Card

Name: Marcus Dole
Chairman
Tel: 0574-71948263
Mobile: 13857420916
Email: kelvora@mailnest.example
Web: www.prt2019.example

LOGO

Font styles to use
Serif
Sans Serif
Decorative

Requirements
Nice to have
• Feels: clean, specifications, safety, comfort, warmth and happiness.

```html
<!DOCTYPE html>
<html lang="en">
<head>
<meta charset="utf-8">
<title>PingRuiTang Business Card</title>
<link rel="stylesheet" href="https://fonts.googleapis.com/css2?family=Montserrat:wght@300;400;600;700;800&display=swap">
<style>
:root{
  --bg:#2b2b2d;
  --card:#000000;
  --blue:#1576c0;
  --pink:#e8068f;
  --white:#ffffff;
}
*{margin:0;padding:0;box-sizing:border-box}
html,body{width:1200px;height:900px;overflow:hidden}
body{background:var(--bg);font-family:"Montserrat",Arial,sans-serif;color:var(--white);
  display:flex;flex-direction:column;align-items:center;justify-content:center;gap:40px}
.card{position:relative;width:700px;height:400px;background:var(--card);border-radius:26px;overflow:hidden;
  box-shadow:0 14px 30px rgba(0,0,0,.45)}
.card-back .brand-mark{position:absolute;left:70px;top:210px;display:flex;align-items:center;gap:14px}
.brand-dot{width:30px;height:30px;border-radius:50%;background:var(--pink)}
.brand-name{font-weight:700;color:var(--blue);font-size:34px;letter-spacing:.5px}
.card-back .website{position:absolute;left:74px;top:290px;font-weight:700;font-size:22px;letter-spacing:.5px}
.website .accent{color:var(--pink)}
.bands{position:absolute;inset:0}
.person{position:absolute;left:38px;top:40px}
.person-name{font-weight:800;font-size:26px;color:var(--blue);letter-spacing:1px}
.person-title{font-weight:700;font-size:13px;letter-spacing:1px;margin-top:2px}
.logo{position:absolute;left:200px;top:120px;width:320px;text-align:center}
.logo-row{display:flex;align-items:center;justify-content:center;gap:12px}
.logo-name{font-weight:700;font-size:46px;color:var(--blue);letter-spacing:.5px}
.tagline{display:flex;align-items:center;gap:10px;margin-top:4px;font-weight:300;font-size:18px}
.tagline::before,.tagline::after{content:"";flex:1;height:2px;background:var(--white)}
.contacts{position:absolute;right:30px;top:150px;list-style:none;text-align:right;font-weight:600;font-size:14.5px;line-height:1.5}
.contacts li{display:flex;align-items:center;justify-content:flex-end;gap:8px}
.contacts svg{width:12px;height:12px;fill:var(--pink);flex:none}
.address{position:absolute;left:34px;top:326px;font-weight:600;font-size:16px;line-height:1.35}
</style>
</head>
<body>
<section class="card card-back" aria-label="Card back">
  <div class="brand-mark"><span class="brand-dot"></span><span class="brand-name">PingRuiTang</span></div>
  <p class="website">www.<span class="accent">prt2019</span>.example</p>
</section>

<section class="card card-front" aria-label="Card front">
  <svg class="bands" viewBox="0 0 700 400" aria-hidden="true">
    <polygon points="0,305 500,305 560,400 0,400" fill="var(--blue)"/>
    <line x1="540" y1="318" x2="700" y2="318" stroke="var(--white)" stroke-width="3"/>
    <polygon points="548,328 700,328 700,400 595,400" fill="var(--pink)"/>
  </svg>
  <div class="person">
    <p class="person-name">MARCUS DOLE</p>
    <p class="person-title">CHAIRMAN</p>
  </div>
  <div class="logo">
    <div class="logo-row"><span class="brand-dot"></span><span class="logo-name">PingRuiTang</span></div>
    <p class="tagline">Training &amp; Services</p>
  </div>
  <ul class="contacts">
    <li>0574-71948263<svg viewBox="0 0 12 12"><path d="M2 1l2 0 1 3-1.5 1a6 6 0 0 0 2.5 2.5L7 6l3 1v2c0 1-1 2-2 2A8 8 0 0 1 1 3c0-1 .5-2 1-2z"/></svg></li>
    <li>13857420916<svg viewBox="0 0 12 12"><path d="M3 0h6a1 1 0 0 1 1 1v10a1 1 0 0 1-1 1H3a1 1 0 0 1-1-1V1a1 1 0 0 1 1-1zm0 2v7h6V2z"/></svg></li>
    <li>kelvora@mailnest.example<svg viewBox="0 0 12 12"><path d="M0 2h12v8H0zm1 1v.5l5 3 5-3V3z"/></svg></li>
    <li>www.prt2019.example<svg viewBox="0 0 12 12"><path d="M6 0a6 6 0 1 0 0 12A6 6 0 0 0 6 0zm0 1.2c.8.8 1.3 2.4 1.4 4.2H4.6C4.7 3.6 5.2 2 6 1.2zM1.3 6.6h2.3c.1 1.6.5 3 1.1 3.9a4.8 4.8 0 0 1-3.4-3.9zm0-1.2a4.8 4.8 0 0 1 3.4-3.9c-.6.9-1 2.3-1.1 3.9zm3.3 1.2h2.8c-.1 1.8-.6 3.4-1.4 4.2-.8-.8-1.3-2.4-1.4-4.2zm3.8 0h2.3a4.8 4.8 0 0 1-3.4 3.9c.6-.9 1-2.3 1.1-3.9zm0-1.2c-.1-1.6-.5-3-1.1-3.9a4.8 4.8 0 0 1 3.4 3.9z"/></svg></li>
  </ul>
  <address class="address" style="font-style:normal">258, LanpingJie<br>BeiyuanQu, Ningbo, Zhejiang</address>
</section>
</body>
</html>
```